Homemaking training schools needs a Business Card design

Designer, Hello!

No special requirements, good-looking enough.
--------------------------------------------------------------------------

Name: Marcus Dole
Chairman
Tel: 0574-71948263
Mobile: 13857420916
Email: kelvora@mailnest.example
Web: www.prt2019.example
Add: No.258, LanpingJie, BeiyuanQu, Ningbo, Zhejiang

LOGO
Ningbo PRT Homemaking Training School

Target Market(s)

pregnant women, mothers, infants, the elderly and families, including cleaning, cooking, nursing training.

Industry/Entity Type

Business

Contact Information for Business Card

Name: Marcus Dole
Chairman
Tel: 0574-71948263
Mobile: 13857420916
Email: kelvora@mailnest.example
Web: www.prt2019.example

LOGO

Font styles to use
Serif
Sans Serif
Decorative

Requirements
Nice to have
• Feels: clean, specifications, safety, comfort, warmth and happiness.

```html
<!DOCTYPE html>
<html lang="en">
<head>
<meta charset="utf-8">
<title>PeiRongTang Business Card</title>
<link href="https://fonts.googleapis.com/css2?family=Quicksand:wght@500;700&family=Open+Sans:wght@400;600;700&display=swap" rel="stylesheet">
<style>
  :root {
    --brand-blue: #1f76bd;
    --ink: #1c1c1c;
    --muted: #555b63;
    --paper: #ffffff;
    --backdrop: #ebe9e5;
  }
  * { margin: 0; padding: 0; box-sizing: border-box; }
  html, body { width: 1200px; height: 900px; overflow: hidden; }
  body { background: var(--backdrop); position: relative; font-family: "Open Sans", Arial, sans-serif; }

  .card {
    position: absolute;
    border-radius: 16px;
    overflow: hidden;
    box-shadow: 0 6px 22px rgba(0,0,0,0.12);
  }
  .card--front { left: 78px; top: 35px; width: 588px; height: 363px; background: var(--paper); }
  .card--back { left: 390px; top: 506px; width: 565px; height: 350px; background: var(--brand-blue); }

  .band { position: absolute; left: 0; width: 100%; }
  .card--front .band { top: 28px; height: 99px; background: var(--brand-blue); }
  .card--back .band { top: 81px; height: 96px; background: var(--paper); }

  .badge-circle { position: absolute; border-radius: 50%; }
  .card--front .badge-circle { left: 238px; top: 18px; width: 114px; height: 114px; background: var(--paper); }
  .card--back .badge-circle { left: 219px; top: 58px; width: 122px; height: 122px; background: var(--brand-blue); }

  .brand { position: absolute; left: 0; width: 100%; text-align: center; }
  .brand__name { font-family: "Quicksand", sans-serif; font-weight: 700; font-size: 40px; letter-spacing: -0.5px; line-height: 1; }
  .brand__tagline { font-family: "Quicksand", sans-serif; font-weight: 500; font-size: 17px; margin-top: 6px; }
  .card--front .brand { top: 130px; }
  .card--front .brand__name { color: var(--brand-blue); }
  .card--front .brand__tagline { color: var(--muted); }
  .card--back .brand { top: 190px; }
  .card--back .brand__name, .card--back .brand__tagline { color: var(--paper); }

  .contacts { position: absolute; right: 338px; top: 232px; list-style: none; text-align: right; }
  .contacts li { font-size: 15px; color: var(--ink); height: 24.5px; line-height: 24.5px; display: flex; justify-content: flex-end; align-items: center; gap: 5px; }
  .contacts svg { width: 12px; height: 12px; fill: var(--brand-blue); flex: none; }

  .person { position: absolute; left: 289px; top: 223px; }
  .person__name { font-size: 20px; font-weight: 700; color: var(--brand-blue); line-height: 1.3; }
  .person__role { font-size: 15px; color: var(--ink); line-height: 1.2; }
  .person__address { font-size: 15px; color: var(--ink); line-height: 25px; margin-top: 19px; font-style: normal; }
</style>
</head>
<body>

<section class="card card--front" aria-label="Business card front">
  <div class="band"></div>
  <div class="badge-circle"></div>
  <div class="brand">
    <div class="brand__name">PeiRongTang</div>
    <div class="brand__tagline">Training &amp; Services</div>
  </div>

  <ul class="contacts">
    <li>0574-71948263
      <svg viewBox="0 0 12 12" aria-hidden="true"><path d="M2.4 1l2 2.2-1 1.3a7 7 0 0 0 4 4l1.3-1 2.3 2-1.3 1.5C5 10.8 1.2 7 .9 2.3z"/></svg>
    </li>
    <li>13857420916
      <svg viewBox="0 0 12 12" aria-hidden="true"><path d="M3 0h6a1 1 0 0 1 1 1v10a1 1 0 0 1-1 1H3a1 1 0 0 1-1-1V1a1 1 0 0 1 1-1zm.5 1.5v8h5v-8z"/></svg>
    </li>
    <li>kelvora@mailnest.example
      <svg viewBox="0 0 12 12" aria-hidden="true"><path d="M0 2h12v1.2L6 7 0 3.2zm0 2.6l6 3.8 6-3.8V10H0z"/></svg>
    </li>
    <li>www.prt2019.example
      <svg viewBox="0 0 12 12" aria-hidden="true"><circle cx="6" cy="6" r="6"/></svg>
    </li>
  </ul>

  <div class="person">
    <div class="person__name">Marcus Dole</div>
    <div class="person__role">Chairman</div>
    <address class="person__address">No.258, LanpingJie,<br>BeiyuanQu, Ningbo, Zhejiang</address>
  </div>
</section>

<section class="card card--back" aria-label="Business card back">
  <div class="band"></div>
  <div class="badge-circle"></div>
  <div class="brand">
    <div class="brand__name">PeiRongTang</div>
    <div class="brand__tagline">Training &amp; Services</div>
  </div>
</section>

</body>
</html>
```